TRESSOVA FACEBOOK DESIGN

I need new design for facebook https://www.facebook.com/tressovalumen.
Our Businnes is Hair care , hair replacement , hair transplant . hair regrowth . i NEED MEDICAL AND PROFESSIONAL DESIGN. I NEED ALSO RESPONSIVE DESIGN

Target Market(s)

Consumers

Industry/Entity Type

MEDICAL AND COSMETICS

Colors
0054AA
0677BA
7BADD7
CADEEF
E8F1F8

Requirements
Must have
• MEDICAL
Nice to have
• RESPONSIVE DESIGN

```html
<!DOCTYPE html>
<html lang="it">
<head>
<meta charset="utf-8">
<title>Tressova — Facebook Cover</title>
<link rel="stylesheet" href="https://fonts.googleapis.com/css2?family=Ubuntu:wght@400;500;700&family=Arimo:wght@700&display=swap">
<style>
  :root {
    --navy: #0054AA;
    --blue: #0677BA;
    --sky: #7BADD7;
    --mist: #CADEEF;
    --ice: #E8F1F8;
    --cyan: #1fa3e0;
    --ink: #1d1d1f;
    --stage: #5a5a5a;
  }
  * { margin: 0; padding: 0; box-sizing: border-box; }
  html, body { width: 1200px; height: 1200px; overflow: hidden; }
  body {
    background: var(--stage);
    display: flex;
    align-items: center;
    justify-content: center;
    font-family: "Ubuntu", sans-serif;
  }
  .cover {
    position: relative;
    width: 1120px;
    height: 426px;
    overflow: hidden;
    background:
      radial-gradient(ellipse 60% 80% at 20% 30%, #ffffff 0%, rgba(255,255,255,0) 70%),
      linear-gradient(100deg, var(--ice) 0%, #d6eaf8 45%, #a9d3f1 75%, #7fc0ec 100%);
  }
  .brand {
    position: absolute;
    left: 70px;
    top: 48px;
    display: flex;
    align-items: center;
    gap: 14px;
  }
  .brand-mark {
    width: 46px;
    height: 46px;
    background: var(--sky);
  }
  .brand-name {
    font-family: "Ubuntu", sans-serif;
    font-weight: 700;
    font-size: 62px;
    line-height: 1;
    color: var(--navy);
    letter-spacing: -1px;
  }
  .tagline {
    position: absolute;
    left: 72px;
    top: 140px;
    font-size: 17px;
    font-weight: 500;
    color: var(--blue);
    letter-spacing: 0.2px;
  }
  .swoosh {
    position: absolute;
    left: 66px;
    top: 160px;
  }
  .hashtags {
    position: absolute;
    left: 70px;
    top: 212px;
    font-family: "Arimo", sans-serif;
    font-weight: 700;
    font-size: 40px;
    line-height: 54px;
    color: var(--ink);
  }
  .services {
    position: absolute;
    left: 446px;
    top: 50px;
    display: flex;
    align-items: center;
    gap: 12px;
    font-weight: 700;
    font-size: 19px;
    color: var(--navy);
    white-space: nowrap;
  }
  .service { display: flex; align-items: center; gap: 5px; }
  .divider { color: var(--navy); font-weight: 400; }
  .visual {
    position: absolute;
    left: 560px;
    top: 84px;
    width: 540px;
    height: 330px;
    border-radius: 28px 28px 0 0;
    background: linear-gradient(160deg, #d9ebf8 0%, #b5d8f1 50%, #8cc3ea 100%);
  }
  .waves { position: absolute; left: 0; bottom: 0; }
</style>
</head>
<body>
  <section class="cover">
    <div class="visual" role="img" aria-label="Photo of a woman with long dark wavy hair beside translucent vitamin bubbles and a hair strand illustration"></div>

    <div class="brand">
      <span class="brand-mark"></span>
      <span class="brand-name">Tressova</span>
    </div>
    <p class="tagline">CURA E REINTEGRAZIONE DEI CAPELLI</p>
    <svg class="swoosh" width="340" height="30" viewBox="0 0 340 30">
      <path d="M4,18 C90,30 230,32 336,4" fill="none" stroke="var(--cyan)" stroke-width="3" stroke-linecap="round"/>
    </svg>

    <div class="hashtags">
      <p>#capellifelici</p>
      <p>#semplicementemigliori</p>
    </div>

    <div class="services">
      <span class="service">
        <svg width="18" height="18" viewBox="0 0 18 18"><circle cx="9" cy="9" r="7.5" fill="none" stroke="var(--navy)" stroke-width="1.6"/><path d="M5.5,9.2 L8,11.6 L12.6,6.6" fill="none" stroke="var(--navy)" stroke-width="1.6" stroke-linecap="round" stroke-linejoin="round"/></svg>
        HAIR CARE
      </span>
      <span class="divider">|</span>
      <span class="service">
        <svg width="18" height="18" viewBox="0 0 18 18"><circle cx="9" cy="9" r="7.5" fill="none" stroke="var(--navy)" stroke-width="1.6"/><path d="M5.5,9.2 L8,11.6 L12.6,6.6" fill="none" stroke="var(--navy)" stroke-width="1.6" stroke-linecap="round" stroke-linejoin="round"/></svg>
        HAIR REPLACEMENT
      </span>
      <span class="divider">|</span>
      <span class="service">
        <svg width="18" height="18" viewBox="0 0 18 18"><circle cx="9" cy="9" r="7.5" fill="none" stroke="var(--navy)" stroke-width="1.6"/><path d="M5.5,9.2 L8,11.6 L12.6,6.6" fill="none" stroke="var(--navy)" stroke-width="1.6" stroke-linecap="round" stroke-linejoin="round"/></svg>
        HAIR TRANSPLANT
      </span>
    </div>

    <svg class="waves" width="1120" height="160" viewBox="0 266 1120 160">
      <defs>
        <linearGradient id="deep" x1="0" y1="0" x2="1" y2="0">
          <stop offset="0" stop-color="var(--navy)"/>
          <stop offset="0.6" stop-color="var(--blue)"/>
          <stop offset="1" stop-color="var(--cyan)"/>
        </linearGradient>
      </defs>
      <path d="M0,338 C250,298 500,328 700,382 C850,418 1000,356 1120,286 L1120,426 L0,426 Z" fill="var(--cyan)"/>
      <path d="M0,352 C250,314 500,342 700,395 C850,428 1000,372 1120,306" fill="none" stroke="#ffffff" stroke-width="3" opacity="0.8"/>
      <path d="M0,366 C250,330 480,360 700,406 C860,438 1000,398 1120,338 L1120,426 L0,426 Z" fill="url(#deep)"/>
    </svg>
  </section>
</body>
</html>
```